Telecommunications/Power civil contractor needs business card design

Were a new telecommunications/power underground civil contractor that is looking for a new business card design. Our company colours are silver or grey and orange. Feel free to use the white background logo or the black background logo.

Target Market(s)

Local contractors, utility companies, private sector mining/energy companies, developers.

Industry/Entity Type

Telecommunications

Contact Information for Business Card

Each card will need the following info:
Persons name:
Title:
E-mail:
Phone number:
Shop Address:
Mailing Address:

Requirements
Must have
• Each card will need the following info:
• Persons name:
• Title:
• E-mail:
• Phone number:
• Shop Address:
• Mailing Address:

```html
<!DOCTYPE html>
<html lang="en">
<head>
<meta charset="utf-8">
<title>Business Card – Trenchline Contracting Inc</title>
<link rel="stylesheet" href="https://fonts.googleapis.com/css2?family=Tenor+Sans&display=swap">
<style>
  :root {
    --page-bg: #e6e6e6;
    --card-white: #ffffff;
    --card-mist: #eeeff0;
    --accent-orange: #d65a2c;
    --steel-grey: #808285;
    --ink: #3c3c3c;
    --rule: #6a6a6a;
  }
  html, body {
    margin: 0;
    width: 1200px;
    height: 1200px;
    overflow: hidden;
    background: var(--page-bg);
  }
  .card {
    position: absolute;
    left: 100px;
    top: 294px;
    width: 1000px;
    height: 611px;
    background: linear-gradient(120deg, var(--card-white) 0%, var(--card-mist) 45%, var(--card-white) 100%);
    font-family: "Tenor Sans", sans-serif;
    color: var(--ink);
    overflow: hidden;
  }
  .person-name {
    position: absolute;
    left: 14px;
    top: 22px;
    margin: 0;
    font-size: 56px;
    font-weight: 400;
    letter-spacing: -1px;
    color: var(--accent-orange);
    line-height: 1;
  }
  .person-title {
    position: absolute;
    left: 15px;
    top: 100px;
    margin: 0;
    font-size: 32px;
    line-height: 1;
  }
  .company-mark {
    position: absolute;
    left: 40px;
    top: 225px;
    width: 380px;
    text-align: center;
  }
  .company-mark svg { display: block; margin: 0 auto 26px; }
  .company-name {
    margin: 0;
    font-size: 40px;
    line-height: 1.1;
    letter-spacing: 1px;
    color: var(--steel-grey);
    font-weight: 400;
  }
  .divider {
    position: absolute;
    left: 453px;
    top: 232px;
    width: 2px;
    height: 298px;
    background: var(--rule);
  }
  .contact {
    position: absolute;
    left: 486px;
    top: 227px;
    margin: 0;
    font-size: 34px;
    line-height: 40px;
    font-style: normal;
  }
  .contact p { margin: 0 0 34px; }
  .contact p:last-child { margin-bottom: 0; }
  .footer-band {
    position: absolute;
    left: 0;
    bottom: 0;
    display: block;
  }
</style>
</head>
<body>
  <article class="card">
    <h1 class="person-name">JOHN DOE</h1>
    <p class="person-title">Director</p>

    <div class="company-mark">
      <svg width="150" height="150" viewBox="0 0 150 150" aria-hidden="true">
        <circle cx="75" cy="75" r="68" fill="none" stroke="var(--accent-orange)" stroke-width="8"/>
      </svg>
      <p class="company-name">TRENCHLINE<br>CONTRACTING INC</p>
    </div>

    <div class="divider"></div>

    <address class="contact">
      <p>1-234-567890<br>john@companyname.com</p>
      <p>Dummy city<br>Dummy Country Land</p>
      <p>123 Dummy St<br>Dummy Centre, Dummy 12345</p>
    </address>

    <svg class="footer-band" width="1000" height="35" viewBox="0 0 1000 35" aria-hidden="true">
      <polygon points="0,0 586,0 604,35 0,35" fill="var(--accent-orange)"/>
      <polygon points="599,0 1000,0 1000,35 617,35" fill="var(--steel-grey)"/>
    </svg>
  </article>
</body>
</html>
```